BildeVOLD buisnesscard

Hey :) I need a modern buisnesscard for my company BildeVOLD
It most have:
Dagligleder og Fotograf: Henrik Audun Strandvik

Mob: +4791264085
Epost: post@bildevold.example
Adresse: Kvernbakken9, 6040 Fjordheim

Facbook and instagram logo with text BildeVOLD

BildeVOLD logo

It Company

```html
<!DOCTYPE html>
<html lang="en">
<head>
<meta charset="utf-8">
<title>BildeVOLD business card</title>
<link href="https://fonts.googleapis.com/css2?family=Titillium+Web:wght@400;700&family=Roboto:wght@300;400&display=swap" rel="stylesheet">
<style>
  :root {
    --backdrop: #3b3430;
    --card-black: #151515;
    --mark-dark: #2c2c2c;
    --card-grey: #a6a8ab;
    --arc-grey: #6e6f72;
    --logo-grey: #9c9da0;
    --ink-white: #ffffff;
  }
  * { margin: 0; padding: 0; box-sizing: border-box; }
  html, body {
    width: 1200px; height: 716px; overflow: hidden;
    background: var(--backdrop);
  }
  .canvas { position: relative; width: 1200px; height: 716px; }
  .card {
    position: absolute; top: 215px;
    width: 500px; height: 286px;
    border-radius: 4px; overflow: hidden;
    box-shadow: 0 10px 28px rgba(0,0,0,.45);
  }
  .card-back {
    left: 70px; background: var(--card-black);
    display: flex; align-items: center; justify-content: center;
  }
  .card-back .brand-name {
    font-family: "Titillium Web", sans-serif; font-weight: 700;
    font-size: 46px; letter-spacing: 1px; color: var(--mark-dark);
  }
  .card-front { left: 630px; background: var(--card-grey); }
  .card-front .panel-shape { position: absolute; inset: 0; }
  .identity { position: absolute; left: 26px; top: 24px; color: var(--ink-white); }
  .identity .person-name {
    font-family: "Titillium Web", sans-serif; font-weight: 700;
    font-size: 17px; line-height: 1.2;
  }
  .identity .person-role {
    font-family: "Roboto", sans-serif; font-weight: 400;
    font-size: 10.5px; margin-top: 2px;
  }
  .contact-list {
    position: absolute; left: 26px; top: 150px; list-style: none;
    font-family: "Roboto", sans-serif; font-weight: 300;
    font-size: 11.5px; color: var(--ink-white);
  }
  .contact-list li { display: flex; align-items: center; gap: 9px; height: 20px; }
  .contact-list svg { width: 11px; height: 11px; flex: none; }
  .social-square {
    width: 11px; height: 11px; background: var(--ink-white); border-radius: 2px; flex: none;
  }
  .front-brand {
    position: absolute; right: 30px; top: 160px;
    font-family: "Titillium Web", sans-serif; font-weight: 700;
    font-size: 38px; letter-spacing: .5px; color: var(--logo-grey);
  }
</style>
</head>
<body>
<main class="canvas">
  <section class="card card-back" aria-label="Business card back">
    <span class="brand-name">BildeVOLD</span>
  </section>

  <section class="card card-front" aria-label="Business card front">
    <svg class="panel-shape" viewBox="0 0 500 286" preserveAspectRatio="none" aria-hidden="true">
      <path d="M322 0 C262 85 262 205 334 286 L500 286 L500 0 Z" fill="var(--card-black)"/>
      <path d="M308 14 C260 95 262 195 318 272" fill="none" stroke="var(--arc-grey)" stroke-width="4" stroke-linecap="round"/>
    </svg>

    <div class="identity">
      <p class="person-name">Henrik Audun Strandvik</p>
      <p class="person-role">Managing Director &amp; Photographer</p>
    </div>

    <ul class="contact-list">
      <li>
        <svg viewBox="0 0 12 12" aria-hidden="true"><rect x="3" y="0.5" width="6" height="11" rx="1.2" fill="none" stroke="#fff" stroke-width="1.2"/><circle cx="6" cy="9.5" r=".7" fill="#fff"/></svg>
        <span>+4791264085</span>
      </li>
      <li>
        <svg viewBox="0 0 12 12" aria-hidden="true"><rect x=".5" y="2.5" width="11" height="7" fill="none" stroke="#fff" stroke-width="1.1"/><path d="M.8 2.8 6 7 11.2 2.8" fill="none" stroke="#fff" stroke-width="1.1"/></svg>
        <span>post@bildevold.example</span>
      </li>
      <li>
        <svg viewBox="0 0 12 12" aria-hidden="true"><path d="M6 11.5 C3 7.5 2 6 2 4.3 A4 4 0 0 1 10 4.3 C10 6 9 7.5 6 11.5Z" fill="#fff"/><circle cx="6" cy="4.4" r="1.5" fill="var(--card-grey)"/></svg>
        <span>Kvernbakken9, 6040 Fjordheim</span>
      </li>
      <li>
        <span class="social-square" aria-hidden="true"></span>
        <span>/BildeVOLD</span>
      </li>
    </ul>

    <span class="front-brand">BildeVOLD</span>
  </section>
</main>
</body>
</html>
```